Website Design Request - Management Consulting Firm

We need a Website designed for an IT Management Staffing and Recruiting firm called TRAVENOK based in San Francisco.

The firm is an high-end technology staffing agency. Our focus is on quality and high-caliber candidates rather than quantity.

The website will have two main home pages. One for the recruiter and another on for the candidates.

The website needs to optimize for mobile devices as well.

I have attached few mock-ups that I have done just to show what I am thinking. The UI needs to be very clean, fluid, and it needs to have a modern, rustic, professional feel to it.

Target Market(s)

Technology Manager, Director, VP, CIO of Companies that have $4b-10b dollar revenue. Such as larkspurdwellings.example , https://www.velmorian.example/, quillnet.example, zib.example

Industry/Entity Type

Management Consulting

Number of Pages Required

5+ page

Font styles to use
Sans Serif

Colors
f37122
ffffff

Requirements
Must have
• Please review mock-ups for suggestions
Nice to have
Should not have

```html
<!DOCTYPE html>
<html lang="en">
<head>
<meta charset="utf-8">
<title>TRAVENOK – IT Project Management Talent</title>
<link rel="stylesheet" href="https://fonts.googleapis.com/css2?family=Open+Sans:wght@400;600;700&display=swap">
<style>
:root{
  --orange:#f37122;
  --white:#ffffff;
  --ink:#2b2b2b;
  --dark:#333333;
  --grey:#7a7a7a;
  --light:#f4f4f4;
  --panel:#efefef;
}
*{margin:0;padding:0;box-sizing:border-box}
html,body{width:691px;height:1200px;overflow:hidden;background:var(--white)}
body{font-family:"Open Sans",sans-serif;color:var(--ink);position:relative}
.abs{position:absolute}

/* header */
.site-header{position:absolute;left:0;top:0;width:691px;height:56px;background:var(--white);box-shadow:0 1px 3px rgba(0,0,0,.08);z-index:3}
.brand{left:57px;top:13px;font-size:23px;font-weight:600;letter-spacing:1px;color:var(--orange)}
.nav a{position:absolute;top:23px;font-size:8px;color:var(--ink);text-decoration:none}
.btn-sign{position:absolute;top:21px;height:17px;font-size:8px;color:var(--white);line-height:17px;text-align:center}
.btn-in{left:544px;width:42px;background:var(--orange)}
.btn-up{left:588px;width:46px;background:var(--dark)}

/* hero */
.hero-pattern{left:0;top:56px;width:327px;height:314px;background:var(--panel)}
.hero-photo{left:328px;top:56px;width:363px;height:288px;background:linear-gradient(160deg,#f7f7f7,#e9e9e9 55%,#d8d2cc)}
.hero-copy{left:79px;top:126px;width:225px}
.hero-copy h1{font-size:11.5px;font-weight:400;line-height:14px;letter-spacing:.2px}
.hero-copy p{font-size:7.6px;line-height:11px;margin-top:5px}
.signup{left:79px;top:190px;display:flex}
.signup .field{width:137px;height:19px;background:var(--white);font-size:5.5px;color:#999;line-height:19px;padding-left:7px}
.signup .go{width:79px;height:19px;margin-left:3px;background:var(--orange);color:var(--white);font-size:8px;font-weight:600;line-height:19px;padding-left:15px}
.terms{left:79px;top:214px;font-size:5.2px;color:var(--grey)}
.terms u,.job u{color:var(--ink)}
.job{left:79px;top:247px}
.job h2{font-size:12px;font-weight:400}
.job p{font-size:6px;color:var(--grey);margin-top:1px}
.pager{left:327px;top:391px}

/* tabs */
.tabs{left:0;top:414px;width:691px;height:33px;background:var(--orange)}
.tab{position:absolute;top:0;height:33px;line-height:33px;font-size:11.5px;color:var(--white);font-weight:600}
.tab.active{left:57px;top:2px;height:31px;width:116px;background:var(--white);color:var(--ink);font-weight:400;text-align:center;line-height:31px}

.focus-intro{left:57px;top:473px;width:577px;font-size:6.8px;line-height:10.3px;color:var(--grey);text-align:center}
.service{top:554px;width:180px;text-align:center}
.bulb{width:46px;height:66px;margin:0 auto;border-radius:23px 23px 6px 6px}
.service h3{font-size:9px;font-weight:400;margin-top:7px}
.service h3.hot{color:var(--orange)}
.service p{font-size:6.6px;line-height:10px;color:var(--grey);margin-top:7px}

/* flexibility */
.flex{left:0;top:726px;width:691px;height:266px;background:var(--dark);color:var(--white)}
.flex h2{position:absolute;top:33px;width:100%;text-align:center;font-size:15px;font-weight:600;letter-spacing:.3px}
.flex .sub{position:absolute;top:53px;width:100%;text-align:center;font-size:9px;color:#ddd}
.roles{position:absolute;top:97px;width:280px}
.roles h3{font-size:11.5px;font-weight:400}
.roles ul{list-style:none;margin-top:15px}
.roles li{font-size:7.3px;line-height:10px;padding-left:16px;position:relative;margin-bottom:10px}
.roles li svg{position:absolute;left:0;top:1px}
.cta{position:absolute;top:212px;height:18px;line-height:18px;font-size:7.5px;color:var(--white);text-align:center}

/* contact */
.contact{left:0;top:992px;width:691px;height:170px;background:var(--light)}
.contact h2{position:absolute;top:40px;width:100%;text-align:center;font-size:12.5px;font-weight:600}
.contact p{position:absolute;top:65px;left:170px;width:351px;text-align:center;font-size:6.5px;line-height:10px;color:var(--grey)}
.ring{position:absolute;width:32px;height:32px;border-radius:50%;background:var(--white);display:flex;align-items:center;justify-content:center}
.detail{position:absolute;top:108px;font-size:11px}

.site-footer{left:0;top:1162px;width:691px;height:38px}
.social{position:absolute;top:17px;width:7px;height:7px;border-radius:50%;background:#9a9a9a}
.copy{position:absolute;right:57px;top:15px;font-size:6.5px;color:var(--grey)}
</style>
</head>
<body>

<header class="site-header">
  <div class="abs brand">TRAVENOK</div>
  <nav class="nav">
    <a style="left:424px">Professionals</a>
    <a style="left:490px">Employers</a>
  </nav>
  <div class="btn-sign btn-in">Sign In</div>
  <div class="btn-sign btn-up">Sign Up</div>
</header>

<div class="abs hero-pattern" role="img" aria-label="Decorative light grey puzzle-piece pattern behind the hero text"></div>
<div class="abs hero-photo" role="img" aria-label="Photo of a recruiter's hand selecting one professional from a row of business people"></div>
<div class="abs hero-copy">
  <h1>HIRE TOP IT PROJECT MANAGEMENT TALENTS</h1>
  <p>Search our network, shortlist candidates, send interview requests &amp; fill positions fast</p>
</div>
<div class="abs signup"><div class="field">Your Business Email Address</div><div class="go">Get Started</div></div>
<div class="abs terms">By entering your email address, you agree to our <u>Terms &amp; Conditions</u></div>
<div class="abs job"><h2>Looking for a job?</h2><p><u>Upload Resume</u> and let companies send you offers</p></div>

<svg class="abs pager" width="40" height="10" viewBox="0 0 40 10" aria-hidden="true">
  <path d="M1 5h14M1 5l4-3M1 5l4 3" stroke="#222" fill="none"/>
  <path d="M22 5h14M36 5l-4-3M36 5l-4 3" stroke="#f37122" fill="none"/>
</svg>

<div class="abs tabs">
  <div class="tab active">Our Focus</div>
  <div class="tab" style="left:215px">Why us</div>
  <div class="tab" style="left:336px">How it works?</div>
</div>

<p class="abs focus-intro">Lorem ipsum dolor sit amet, consectetur adipiscing elit. Etiam consequat orci diam, ullamcorper semper nisl pellentesque finibus. Pellentesque tincidunt enim eget suscipit varius. Donec hendrerit arcu nibh, sit amet gravida ligula facilisis nec. Proin sit amet bibendum ligula, at semper erat. Nunc vehicula posuere malesuada. Ut laoreet, turpis eu accumsan ultricies, eros elit maximus tellus, blandit pellentesque nulla mi sit amet purus. Ut placerat ante ut arcu interdum, vitae tristique arcu malesuada. Suspendisse at magna sem. Quisque ultricies fringilla lacus, at placerat nibh feugiat vel. Etiam bibendum cursus est, sed euismod metus iaculis et. Vestibulum varius, lectus vitae mollis finibus, mauris lorem scelerisque neque, at maximus nunc enim id ipsum. Aliquam ut viverra metus, eget convallis lorem.</p>

<div class="abs service" style="left:57px">
  <div class="bulb" style="background:var(--dark)" role="img" aria-label="Dark lightbulb illustration with a person symbol"></div>
  <h3 class="hot">Project Managers</h3>
  <p>Manage IT Projects, Programs and Portfolio from start to finish.<br>Get your projects back or track with our highly vetted consultants.<br>Conduct Project audits, lessons learned and post-mortem.</p>
</div>
<div class="abs service" style="left:256px">
  <div class="bulb" style="background:var(--orange)" role="img" aria-label="Orange lightbulb illustration with an organisation chart symbol"></div>
  <h3>PMO Leadership</h3>
  <p>Stand up IT PMO office and project governance.<br>Re-vamp or optimize existing IT Project Management Processes.<br>Temporarily run IT PMO through our highly qualified PM Leaders</p>
</div>
<div class="abs service" style="left:456px">
  <div class="bulb" style="background:var(--orange)" role="img" aria-label="Orange lightbulb illustration with a group of people symbol"></div>
  <h3>PM Trainer &amp; Coaches</h3>
  <p>Individual coaching or group project management training.<br>Setup Project Portfolio Management Tools.<br>Drive Project Management Governance and adoption.</p>
</div>

<section class="abs flex">
  <h2>HIRING FLEXIBILITY</h2>
  <div class="sub">Hire on hourly basis or bring them on as permanent employees</div>
  <div class="roles" style="left:57px">
    <h3>Contract Roles</h3>
    <ul>
      <li><svg width="8" height="8" viewBox="0 0 8 8"><circle cx="4" cy="4" r="3.2" stroke="#fff" fill="none"/><path d="M4 2v2h1.5" stroke="#fff" fill="none"/></svg>Flexible hourly rote. Ideal for contract, port-time, or interim positions. Structure as needed.</li>
      <li><svg width="8" height="8" viewBox="0 0 8 8"><ellipse cx="4" cy="1.5" rx="3.5" ry="1.4" fill="#fff"/><rect x=".5" y="3" width="7" height="2" fill="#fff"/><rect x=".5" y="5.7" width="7" height="2" fill="#fff"/></svg>Search our database and schedule interviews directly</li>
      <li><svg width="8" height="8" viewBox="0 0 8 8"><path d="M0 0h8L5 4v4L3 7V4z" fill="#fff"/></svg>25% Cheaper than traditional staffing firms.</li>
    </ul>
  </div>
  <div class="roles" style="left:354px">
    <h3>Permanent Roles</h3>
    <ul>
      <li><svg width="8" height="8" viewBox="0 0 8 8"><circle cx="4" cy="4" r="3.6" fill="#fff"/></svg>National Reach - find the best candidate in the nation,</li>
      <li><svg width="9" height="8" viewBox="0 0 9 8"><rect x=".5" y="1.5" width="8" height="5" stroke="#fff" fill="none"/><circle cx="4.5" cy="4" r="1.3" fill="#fff"/></svg>50% cheaper than traditiaanl recruiting fees.</li>
      <li><svg width="8" height="8" viewBox="0 0 8 8"><path d="M0 3.5h2V8H0zM2.5 3.5L4.5 0c1 0 1 1 .8 2.5H8l-.8 5.5H2.5z" fill="#fff"/></svg>White glove services for all permanent roles</li>
    </ul>
  </div>
  <div class="cta" style="left:57px;width:113px;background:var(--orange)">Search For Our Network</div>
  <div class="cta" style="left:354px;width:72px;background:#555">Contact Us</div>
</section>

<section class="abs contact">
  <h2>INTERESTED? CONTACT US!</h2>
  <p>Pharetra libero non facilisis imperdiet, mi augue feugiat sit amet mollis enim velit. Vestibulum fringilla nulla sem maecenas ultrices faucibus felis. Sed nec arcu. Fusce ut felis. Maecenas aenean mollis.</p>
  <div class="ring" style="left:191px;top:101px"><svg width="10" height="10" viewBox="0 0 10 10"><path d="M2 0l2 2.5-1.2 1.3a6 6 0 0 0 3.4 3.4L7.5 6 10 8 8.5 10C4 10 0 6 0 1.5z" fill="#333"/></svg></div>
  <div class="detail" style="left:238px">08-555 010 24</div>
  <div class="ring" style="left:330px;top:101px"><svg width="12" height="9" viewBox="0 0 12 9"><rect width="12" height="9" rx="1" fill="#333"/><path d="M0 1l6 4 6-4" stroke="#fff" fill="none"/></svg></div>
  <div class="detail" style="left:376px">hello@travenok.example</div>
</section>

<footer class="abs site-footer">
  <span class="social" style="left:56px"></span>
  <span class="social" style="left:73px"></span>
  <span class="social" style="left:92px"></span>
  <span class="social" style="left:110px"></span>
  <div class="copy">Your Site © 2016, All rights reserved</div>
</footer>

</body>
</html>
```